Website Development for vaultmerrow.com.au

Build a new Wordpress/Responsive website for vaultmerrow.com.au

Target Market(s)

Compliance Managers, Risk Managers, Information Security and Cyber Security Professionals, Chief Data/Digital Officers, Chief Operating/Financial Officers, Business Continuity Professionals, Disaster Recovery Planners, Small Business Owners, Local/Federal Government entities

Industry/Entity Type

Data Service

Coding

Coded - Design and coding required

Number of Pages Required

5+ page

Font styles to use
Sans Serif

Colors

Designer to choose colors to be used in the design.

Requirements
Must have
• 1. Site Structure: Home Page plus the following chapter-pages for a) Services b) About c) Resources d) Blog e) Contact Us
• 2. Prefer site to built on wordpress and we can purchase a theme if needed (we currently use Kelp9 for other sites)
• 3. Blog needs to be wordpress based
• 4. We will host the site ourselves on our own servers
• 5. Responsive Design
Nice to have
• 1. Livechat capability/interface
• 2. Capability for marketing automation integration (such as hubspot, marketo, infusionsoft etc)
• 3. Capability for CRM integration (Salesforce)

```html
<!DOCTYPE html>
<html lang="en">
<head>
<meta charset="utf-8">
<title>Vault Merrow — Home</title>
<link href="https://fonts.googleapis.com/css2?family=Lato:wght@300;400;700;900&display=swap" rel="stylesheet">
<style>
:root{
  --red:#e41e26;
  --red-deep:#c8141c;
  --ink:#222226;
  --grey:#5b5b5f;
  --black:#0d0d0f;
  --muted:#6a6a6a;
  --white:#ffffff;
  --line:#d9d9d9;
}
*{box-sizing:border-box;margin:0;padding:0}
html,body{width:1200px;height:3766px;overflow:hidden}
body{position:relative;background:var(--white);font-family:'Lato',Arial,sans-serif;color:var(--ink)}
.abs{position:absolute}

/* hero */
.hero{left:0;top:0;width:1200px;height:700px;background:radial-gradient(ellipse at 65% 45%,#2d5a7a 0%,#15324a 40%,#08141f 85%)}
.brand{left:150px;top:38px;display:flex;align-items:center;gap:10px;color:var(--white);font-weight:900;font-size:22px;letter-spacing:1px;white-space:nowrap}
.brand-mark{width:30px;height:30px;border-radius:50%;background:var(--red)}
.nav{left:440px;top:44px;font-size:16px;font-weight:700;color:#cfd6dd;letter-spacing:.5px}
.nav a{color:inherit;text-decoration:none;position:absolute;white-space:nowrap}
.nav .active{color:var(--white)}
.hero-title{left:0;width:1200px;text-align:center;color:var(--white)}
.hero-kicker{top:250px;font-size:48px;font-weight:300;letter-spacing:3px}
.hero-main{top:296px;font-size:64px;font-weight:900;letter-spacing:3px}
.slide-btn{top:281px;width:60px;height:60px;border-radius:50%;background:rgba(160,160,160,.55);display:flex;align-items:center;justify-content:center}

/* section headings */
.heading{left:0;width:1200px;text-align:center;font-size:36px;font-weight:900;color:var(--ink);letter-spacing:.5px}

/* services */
.service{width:302px;height:208px;padding:0 38px}
.service.featured{background:var(--red);box-shadow:0 8px 22px rgba(228,30,38,.35);color:var(--white)}
.service svg{position:absolute;top:0;left:38px}
.service h3{position:absolute;top:76px;left:38px;font-size:20px;font-weight:900;white-space:nowrap}
.service p{position:absolute;top:112px;left:38px;width:250px;font-size:13px;line-height:19px;color:var(--muted)}
.service.featured p{color:#ffe3e3}

/* about */
.about{left:0;top:1348px;width:1200px;height:547px;background:radial-gradient(ellipse at 70% 50%,#707075 0%,var(--grey) 70%)}
.about-art{left:226px;top:1440px;width:300px;height:400px;border-radius:20px 20px 150px 150px;background:linear-gradient(160deg,#2a3f66,#0e1a30)}
.section-title{font-size:34px;font-weight:900;color:var(--white);white-space:nowrap}
.body-copy{font-size:16px;line-height:27px;color:#ececec}
.btn-outline{display:flex;align-items:center;justify-content:center;border:2px solid var(--white);color:var(--white);font-weight:900;font-size:17px;letter-spacing:.5px}

/* resources */
.resources{left:0;top:1895px;width:1200px;height:530px;background:linear-gradient(90deg,#050506 0%,#141416 50%,#2a2a2e 100%)}
.resources-art{left:577px;top:1905px;width:455px;height:440px;background:radial-gradient(ellipse at 50% 55%,#4a4a50 0%,#1c1c20 70%,rgba(20,20,22,0) 100%)}

/* blogs */
.post{width:272px;height:340px;background:var(--white);box-shadow:0 3px 12px rgba(0,0,0,.18)}
.post-img{height:163px;background:linear-gradient(135deg,#3a4a5c,#121a24)}
.post-date{position:absolute;left:18px;top:175px;width:50px;height:46px;background:var(--red);color:var(--white);text-align:center;font-weight:900;font-size:18px;line-height:24px;padding-top:2px}
.post-date span{display:block;font-size:11px;line-height:14px}
.post h4{position:absolute;left:82px;top:175px;width:175px;font-size:16px;line-height:20px;font-weight:900;color:var(--ink)}
.post p{position:absolute;left:20px;top:235px;width:235px;font-size:11px;line-height:16px;color:var(--muted)}
.post .more{position:absolute;left:20px;top:300px;font-size:11px;font-weight:900;color:var(--ink)}

/* contact */
.contact-left{left:0;top:2995px;width:600px;height:600px;background:linear-gradient(135deg,#1a1a1c,#0c0c0d)}
.contact-right{left:600px;top:2995px;width:600px;height:600px;background:linear-gradient(135deg,#e82830,var(--red-deep))}
.contact-item{left:168px;color:var(--white)}
.contact-item svg{position:absolute;left:0;top:0}
.contact-item b{position:absolute;left:60px;top:0;font-size:17px;font-weight:900;white-space:nowrap}
.contact-item span{position:absolute;left:60px;top:24px;font-size:17px;white-space:nowrap}
.field{left:645px;width:412px;border:1.5px solid rgba(255,255,255,.75);color:var(--white);font-size:14px;font-weight:700;padding:10px 14px;letter-spacing:.5px}
.submit{left:645px;top:3386px;width:191px;height:51px;background:#111;color:var(--white);font-weight:900;font-size:18px;display:flex;align-items:center;justify-content:center}

/* footer */
.copyright{left:0;top:3640px;width:1200px;text-align:center;font-size:15px;color:#555}
.social{top:3680px;width:34px;height:34px;border-radius:50%;background:#555}
.chat{left:868px;top:3640px;width:196px;height:45px;border:2px solid var(--red);color:var(--red);font-weight:900;font-size:15px;display:flex;align-items:center;justify-content:center;gap:8px}
.page-badge{width:60px;height:60px;border-radius:50%;background:var(--red);border:5px solid var(--white);box-shadow:0 0 0 2px var(--red)}
</style>
</head>
<body>

<!-- Hero -->
<section class="abs hero" role="img" aria-label="Photo of a hand touching a glowing digital security interface with padlock icons"></section>
<div class="abs brand"><span class="brand-mark"></span>VAULT MERROW</div>
<nav class="abs nav">
  <a class="active" style="left:0">HOME</a>
  <a style="left:88px">SERVICES</a>
  <a style="left:203px">ABOUT</a>
  <a style="left:296px">RESOURCES</a>
  <a style="left:429px">BLOG</a>
  <a style="left:511px">CONTACT</a>
</nav>
<div class="abs hero-title hero-kicker">WELCOME TO</div>
<div class="abs hero-title hero-main">VAULT MERROW</div>
<div class="abs slide-btn" style="left:98px"><svg width="20" height="20" viewBox="0 0 20 20"><path d="M13 3 6 10l7 7" fill="none" stroke="#222" stroke-width="3"/></svg></div>
<div class="abs slide-btn" style="left:1052px"><svg width="20" height="20" viewBox="0 0 20 20"><path d="M7 3l7 7-7 7" fill="none" stroke="#222" stroke-width="3"/></svg></div>
<svg class="abs" style="left:582px;top:405px" width="36" height="52" viewBox="0 0 36 52"><path d="M18 2v46M4 34l14 14 14-14" fill="none" stroke="#fff" stroke-width="3"/></svg>

<svg class="abs" style="left:0;top:580px" width="1200" height="130" viewBox="0 0 1200 130">
  <polygon points="0,8 600,100 1200,8 1200,130 0,130" fill="#fff"/>
  <polyline points="0,8 600,100 1200,8" fill="none" stroke="#e41e26" stroke-width="12"/>
</svg>
<div class="abs page-badge" style="left:570px;top:660px"></div>

<!-- Services -->
<h2 class="abs heading" style="top:756px">OUR SERVICES</h2>

<div class="abs service featured" style="left:130px;top:841px">
  <svg width="60" height="60" viewBox="0 0 60 60" style="top:12px"><circle cx="30" cy="26" r="18" fill="none" stroke="#fff" stroke-width="3"/><path d="M18 52h24M30 44v8" stroke="#fff" stroke-width="3"/></svg>
  <h3>Risk Management</h3>
  <p>Lorem ipsum dolor sit amet consect-etuer adipiscing elit Nam cursus Morbi ut mi Nullam enim leo egestas</p>
</div>
<div class="abs service" style="left:469px;top:841px">
  <svg width="60" height="66" viewBox="0 0 60 66"><rect x="6" y="14" width="48" height="34" rx="3" fill="none" stroke="#e41e26" stroke-width="3"/><path d="M18 58h24M30 48v10" stroke="#222" stroke-width="3"/><rect x="22" y="24" width="16" height="14" fill="none" stroke="#222" stroke-width="3"/></svg>
  <h3>Cyber Security</h3>
  <p>Lorem ipsum dolor sit amet consect-etuer adipiscing elit Nam cursus Morbi ut mi Nullam enim leo egestas</p>
</div>
<div class="abs service" style="left:770px;top:841px">
  <svg width="66" height="66" viewBox="0 0 66 66"><circle cx="33" cy="30" r="24" fill="none" stroke="#e41e26" stroke-width="3"/><path d="M9 30h48M33 6v48" stroke="#222" stroke-width="2"/><path d="M25 60h16" stroke="#222" stroke-width="3"/></svg>
  <h3>Information Security</h3>
  <p>Lorem ipsum dolor sit amet consect-etuer adipiscing elit Nam cursus Morbi ut mi Nullam enim leo egestas</p>
</div>
<div class="abs service" style="left:130px;top:1092px">
  <svg width="60" height="66" viewBox="0 0 60 66"><rect x="8" y="8" width="40" height="52" rx="3" fill="none" stroke="#e41e26" stroke-width="3"/><path d="M16 24h24M16 34h24M16 44h14" stroke="#222" stroke-width="3"/></svg>
  <h3>Disaster Recovery</h3>
  <p>Lorem ipsum dolor sit amet consect-etuer adipiscing elit Nam cursus Morbi ut mi Nullam enim leo egestas</p>
</div>
<div class="abs service" style="left:469px;top:1092px">
  <svg width="66" height="66" viewBox="0 0 66 66"><circle cx="26" cy="36" r="16" fill="none" stroke="#222" stroke-width="3"/><circle cx="46" cy="20" r="12" fill="none" stroke="#e41e26" stroke-width="3"/><path d="M20 36l5 5 8-10" fill="none" stroke="#e41e26" stroke-width="3"/></svg>
  <h3>Compliance Management</h3>
  <p>Lorem ipsum dolor sit amet consect-etuer adipiscing elit Nam cursus Morbi ut mi Nullam enim leo egestas</p>
</div>
<div class="abs service" style="left:770px;top:1092px">
  <svg width="66" height="66" viewBox="0 0 66 66"><rect x="6" y="12" width="54" height="38" rx="3" fill="none" stroke="#222" stroke-width="3"/><path d="M33 18l12 5v9c0 7-6 11-12 13-6-2-12-6-12-13v-9z" fill="none" stroke="#e41e26" stroke-width="3"/><path d="M22 60h22" stroke="#222" stroke-width="3"/></svg>
  <h3>Data Security</h3>
  <p>Lorem ipsum dolor sit amet consect-etuer adipiscing elit Nam cursus Morbi ut mi Nullam enim leo egestas</p>
</div>

<!-- About -->
<section class="abs about"></section>
<svg class="abs" style="left:0;top:1340px" width="1200" height="120" viewBox="0 0 1200 120">
  <polygon points="0,0 1200,0 1200,111 600,8 0,111" fill="#fff"/>
  <polyline points="0,111 600,8 1200,111" fill="none" stroke="#e41e26" stroke-width="10"/>
</svg>
<div class="abs about-art" role="img" aria-label="Illustration of a hand holding a padlock over a circuit board, framed in a shield"></div>
<h2 class="abs section-title" style="left:582px;top:1484px">ABOUT VAULT MERROW</h2>
<p class="abs body-copy" style="left:584px;top:1542px;width:490px">Pellentesque faucibus Ut accumsan ultricies elit Maecenas at justo id velit placerat molestie Donec dictum lectus non odio Cras a ante vitae enim iaculis aliquam Mauris nunc quam venenatis nec euismod sit amet egestas placerat est Pellentesque habitant morbi tristique senectus et netus et malesuada fames ac turpis egestas Cras id</p>
<div class="abs btn-outline" style="left:590px;top:1737px;width:193px;height:55px">READ MORE</div>

<!-- Resources -->
<section class="abs resources"></section>
<div class="abs resources-art" role="img" aria-label="Illustration of a laptop with a fingerprint scan, padlocks and a security shield"></div>
<h2 class="abs section-title" style="left:166px;top:1996px">RESOURCES</h2>
<p class="abs body-copy" style="left:166px;top:2050px;width:420px">Pellentesque faucibus Ut accumsan ultricies elit Maecenas Cras a ante vitae enim iaculis aliquam Mauris nunc quam venenatis nec euismod sit amet egestas placerat est Pellentesque habitant morbi tris</p>
<div class="abs btn-outline" style="left:166px;top:2189px;width:173px;height:50px">READ MORE</div>
<svg class="abs" style="left:0;top:2335px" width="1200" height="110" viewBox="0 0 1200 110">
  <polygon points="0,12 600,88 1200,12 1200,110 0,110" fill="#fff"/>
  <polyline points="0,12 600,88 1200,12" fill="none" stroke="#e41e26" stroke-width="10"/>
</svg>
<div class="abs page-badge" style="left:570px;top:2405px"></div>

<!-- Blogs -->
<h2 class="abs heading" style="top:2506px">RECENT BLOGS</h2>
<article class="abs post" style="left:153px;top:2578px">
  <div class="post-img" role="img" aria-label="Photo of a businessman stopping a row of falling dominoes"></div>
  <div class="post-date">02<span>JAN</span></div>
  <h4>Pellentesque faucibus Ut accumsan ultric</h4>
  <p>Duis quam Nam eget lacus Aliquam erat volutpat Quisque dignissim congue leo Mauris vel lacus vitae felis vestibulum</p>
  <div class="more">READ MORE</div>
</article>
<article class="abs post" style="left:459px;top:2578px">
  <div class="post-img" role="img" aria-label="Photo of a glowing padlock on a digital background held in a hand"></div>
  <div class="post-date">02<span>JAN</span></div>
  <h4>Pellentesque faucibus Ut accumsan ultric</h4>
  <p>Duis quam Nam eget lacus Aliquam erat volutpat Quisque dignissim congue leo Mauris vel lacus vitae felis vestibulum</p>
  <div class="more">READ MORE</div>
</article>
<article class="abs post" style="left:763px;top:2578px">
  <div class="post-img" role="img" aria-label="Photo of a hand touching a data protection shield interface"></div>
  <div class="post-date">02<span>JAN</span></div>
  <h4>Pellentesque faucibus Ut accumsan ultric</h4>
  <p>Duis quam Nam eget lacus Aliquam erat volutpat Quisque dignissim congue leo Mauris vel lacus vitae felis vestibulum</p>
  <div class="more">READ MORE</div>
</article>

<!-- Contact -->
<section class="abs contact-left"></section>
<section class="abs contact-right"></section>
<h2 class="abs section-title" style="left:168px;top:3082px">CONTACT US</h2>
<div class="abs contact-item" style="top:3164px">
  <svg width="40" height="44" viewBox="0 0 40 44"><path d="M20 40S6 24 6 15a14 14 0 0 1 28 0c0 9-14 25-14 25z" fill="none" stroke="#fff" stroke-width="2.5"/><circle cx="20" cy="15" r="5" fill="none" stroke="#fff" stroke-width="2.5"/></svg>
  <b>ADDRESS</b><span>42 Harlow Lane Suite 7 Austin TX 78701</span>
</div>
<div class="abs contact-item" style="top:3248px">
  <svg width="40" height="44" viewBox="0 0 40 44"><path d="M10 4l7 8-4 5c3 6 7 10 13 13l5-4 8 7-5 6C20 39 5 24 4 10z" fill="none" stroke="#fff" stroke-width="2.5"/></svg>
  <b>PHONE NUMBER</b><span>512.555.0148</span>
</div>
<div class="abs contact-item" style="top:3332px">
  <svg width="44" height="40" viewBox="0 0 44 40"><rect x="3" y="8" width="38" height="26" fill="none" stroke="#fff" stroke-width="2.5"/><path d="M3 8l19 15 19-15" fill="none" stroke="#fff" stroke-width="2.5"/></svg>
  <b>EMAIL US</b><span>hello@vaultmerrow.com.au</span>
</div>
<div class="abs field" style="top:3083px;height:45px">NAME</div>
<div class="abs field" style="top:3143px;height:45px">EMAIL</div>
<div class="abs field" style="top:3203px;height:45px">PHONE</div>
<div class="abs field" style="top:3263px;height:100px">MESSAGE</div>
<div class="abs submit">SUBMIT</div>

<svg class="abs" style="left:0;top:3468px" width="1200" height="140" viewBox="0 0 1200 140">
  <polygon points="0,10 600,95 1200,10 1200,140 0,140" fill="#fff"/>
  <polyline points="0,10 600,95 1200,10" fill="none" stroke="#8a8a8a" stroke-width="12"/>
</svg>
<div class="abs page-badge" style="left:570px;top:3555px"></div>

<!-- Footer -->
<div class="abs copyright">© 2019 Company Name  All right reserved</div>
<div class="abs social" style="left:515px"></div>
<div class="abs social" style="left:563px"></div>
<div class="abs social" style="left:613px"></div>
<div class="abs social" style="left:661px"></div>
<div class="abs chat"><svg width="22" height="20" viewBox="0 0 22 20"><path d="M11 2C5 2 1 5.5 1 9.5c0 2.3 1.3 4.3 3.4 5.6L3 19l5-2.6c1 .2 2 .3 3 .3 6 0 10-3.4 10-7.2S17 2 11 2z" fill="#e41e26"/></svg>LIVE CHAT NOW</div>

</body>
</html>
```